International oil and gas consultancy needs a business card design

We need a business card design for a new oil and gas consultancy business based in Perth Australia. This is a professional services business and needs a moderately conservative type of business card. The business card also needs to be simple and uncluttered. The colour of the business logo is dark red (see attached file).
The front of the card should have a white background and mainly black lettering and perhaps some use of dark red and/or grey (your choice).
The back of the card should have a light grey background with dark red, black and or both dark red & black lettering (your choice).
Please find attached a clear brief of how I would like the business card designed.
Updates

Hello Everyone, I have slightly modified the brief. The main change is to incorporate some dark red and grey colours into the card, while still keeping the black lettering dominant. I have made the changes in the attached detailed brief document. Regards

Please note, the front of the card must say Harbour Ledger Services (in addition to the logo).

Industry/Entity Type

Conservative

Requirements
Must have
• brief has been updated. please refer to attachment for details.

Front of the card MUST say Harbour Ledger Services (in addition to the logo)

```html
<!DOCTYPE html>
<html lang="en">
<head>
<meta charset="utf-8">
<title>Harbour Ledger Services – Business Card</title>
<link rel="stylesheet" href="https://fonts.googleapis.com/css2?family=Exo+2:wght@400;500;600&display=swap">
<style>
  :root {
    --brand-red: #9b1b1f;
    --ink: #2a2a2a;
    --ink-soft: #555555;
    --card-white: #f7f7f7;
    --backdrop: #e4e2df;
    --on-red: #ffffff;
  }
  * { margin: 0; padding: 0; box-sizing: border-box; }
  html, body {
    width: 1200px; height: 899px; overflow: hidden;
    background: var(--backdrop);
    font-family: "Exo 2", Arial, sans-serif;
  }
  .card {
    position: absolute; left: 100px; top: 164px;
    width: 1000px; height: 571px;
    border-radius: 44px; overflow: hidden;
    background: radial-gradient(circle at 45% 45%, #ffffff 0%, var(--card-white) 70%, #ececec 100%);
    box-shadow: 0 10px 30px rgba(0,0,0,.18);
  }
  .card__swoosh { position: absolute; inset: 0; width: 100%; height: 100%; }
  .company-name {
    position: absolute; left: 90px; top: 190px;
    font-size: 40px; font-weight: 600; color: var(--brand-red);
    letter-spacing: .5px;
  }
  .person { position: absolute; left: 110px; top: 318px; color: var(--ink); }
  .person__name { font-size: 26px; font-weight: 500; letter-spacing: 1.5px; text-transform: uppercase; }
  .person__title { font-size: 17px; color: var(--ink-soft); margin-top: 2px; padding-left: 14px; }
  .address {
    position: absolute; left: 150px; top: 430px;
    font-size: 22px; line-height: 1.45; color: var(--ink);
  }
  .contact {
    position: absolute; right: 56px; top: 128px;
    list-style: none; text-align: right; color: var(--on-red);
    font-size: 19px; line-height: 1.9;
  }
  .contact li { display: flex; justify-content: flex-end; align-items: center; gap: 12px; }
  .contact svg { width: 18px; height: 18px; fill: var(--on-red); }
  .contact__plain { padding-right: 30px; }
</style>
</head>
<body>
  <div class="card">
    <svg class="card__swoosh" viewBox="0 0 1000 571" preserveAspectRatio="none" aria-hidden="true">
      <path d="M655 0 C640 250 470 470 230 571 L1000 571 L1000 0 Z" fill="var(--brand-red)"/>
      <path d="M608 0 C610 150 560 300 470 395 C560 310 625 160 630 0 Z" fill="var(--brand-red)"/>
    </svg>

    <div class="company-name">Harbour Ledger Services</div>

    <div class="person">
      <div class="person__name">Martin Keane</div>
      <div class="person__title">Managing Director</div>
    </div>

    <div class="address">Level 18, 240 Quay Street<br>Perth WA</div>

    <ul class="contact">
      <li>08 6150 2274
        <svg viewBox="0 0 24 24"><path d="M6.6 10.8a15 15 0 0 0 6.6 6.6l2.2-2.2c.3-.3.7-.4 1-.2 1.1.4 2.3.6 3.6.6.6 0 1 .4 1 1V20c0 .6-.4 1-1 1A17 17 0 0 1 3 4c0-.6.4-1 1-1h3.5c.6 0 1 .4 1 1 0 1.3.2 2.5.6 3.6.1.3 0 .7-.2 1z"/></svg></li>
      <li>08 6150 2275
        <svg viewBox="0 0 24 24"><path d="M7 1h10a2 2 0 0 1 2 2v18a2 2 0 0 1-2 2H7a2 2 0 0 1-2-2V3a2 2 0 0 1 2-2zm0 3v14h10V4zm5 15.5a1 1 0 1 0 0 2 1 1 0 0 0 0-2z"/></svg></li>
      <li>08 6150 2276
        <svg viewBox="0 0 24 24"><path d="M6 2h10v5H6zM3 8h18v10h-3v4H6v-4H3zm5 7v5h8v-5z"/></svg></li>
      <li>info@harbourledger.com
        <svg viewBox="0 0 24 24"><path d="M2 5h20v14H2zm2 2v.5l8 5 8-5V7z"/></svg></li>
      <li>www.harbourledger.com
        <svg viewBox="0 0 24 24"><path d="M12 2a10 10 0 1 0 0 20 10 10 0 0 0 0-20zm6.9 6h-3a15 15 0 0 0-1.3-3.9A8 8 0 0 1 18.9 8zM12 4c.8 1.2 1.4 2.5 1.8 4h-3.6c.4-1.5 1-2.8 1.8-4zM4.3 14a8 8 0 0 1 0-4h3.4a16 16 0 0 0 0 4zm.8 2h3a15 15 0 0 0 1.3 3.9A8 8 0 0 1 5.1 16zm3-8h-3a8 8 0 0 1 4.3-3.9C8.7 5.3 8.3 6.6 8.1 8zM12 20c-.8-1.2-1.4-2.5-1.8-4h3.6c-.4 1.5-1 2.8-1.8 4zm2.3-6H9.7a14 14 0 0 1 0-4h4.6a14 14 0 0 1 0 4zm.3 5.9c.6-1.2 1-2.5 1.3-3.9h3a8 8 0 0 1-4.3 3.9zm1.7-5.9a16 16 0 0 0 0-4h3.4a8 8 0 0 1 0 4z"/></svg></li>
    </ul>
  </div>
</body>
</html>
```